Business cards to launch an education platform

Hi,
I am looking at having new business cards designed.
I am a startup, developing a web platform for schools and university, the education world. It's an online assessment system.
I would like a card that looks classy, and that is using the colors and the font of my logo.

I have attached:
1) my logo
2) A business card that I have designed quickly so you can have all the information required in the card, but I really don't like it.
3) The font that I am using (Lato Regular) to design my web platform
4) Some screenshots of my web platform so you can have a look at the style that I have.

Target Market(s)

Major market: Education system: Schools and university
Minor markets: Business in general

Industry/Entity Type

Business

Contact Information for Business Card

Clara Fenwick
Director

M: 0437 518 902
E: clara.fenwick@amberLoomSystems.com.au

Requirements
Must have
• The colors of my logo

```html
<!DOCTYPE html>
<html lang="en">
<head>
<meta charset="UTF-8">
<title>Amber Loom Systems – Business Cards</title>
<link rel="stylesheet" href="https://fonts.googleapis.com/css2?family=Lato:wght@400;700&display=swap">
<style>
  :root {
    --canvas-bg: #e9e6e1;
    --card-white: #ffffff;
    --ink-navy: #1f3f78;
    --brand-blue: #1d86c8;
    --brand-blue-light: #45b0da;
    --brand-blue-deep: #0f5fae;
    --card-black: #0b0b0c;
    --text-white: #ffffff;
  }
  * { box-sizing: border-box; margin: 0; padding: 0; }
  html, body { width: 1200px; height: 892px; overflow: hidden; }
  body {
    background: var(--canvas-bg);
    font-family: "Lato", sans-serif;
    position: relative;
  }
  .card {
    position: absolute;
    top: 291px;
    width: 540px;
    height: 309px;
    border-radius: 4px;
    overflow: hidden;
    box-shadow: 0 6px 18px rgba(0,0,0,0.18);
  }
  .card-front { left: 620px; background: var(--card-white); }
  .card-back { left: 40px; background: var(--card-black); }

  .card-shape { position: absolute; inset: 0; width: 100%; height: 100%; }

  .brand {
    position: absolute;
    display: flex;
    align-items: center;
    gap: 12px;
    white-space: nowrap;
  }
  .brand-mark {
    flex-shrink: 0;
    width: 32px;
    height: 32px;
    background: var(--brand-blue);
  }
  .brand-name {
    font-weight: 400;
    font-size: 24px;
    letter-spacing: 2px;
    line-height: 1.1;
  }
  .card-front .brand { top: 24px; right: 26px; }
  .card-front .brand-name { color: var(--ink-navy); }
  .card-back .brand { top: 50%; left: 50%; transform: translate(-50%, -50%); }
  .card-back .brand-mark { width: 40px; height: 40px; }
  .card-back .brand-name { color: var(--brand-blue); font-size: 28px; }

  .contact {
    position: absolute;
    right: 26px;
    bottom: 22px;
    text-align: right;
    color: var(--text-white);
    white-space: nowrap;
  }
  .contact-name { font-size: 36px; font-weight: 400; line-height: 1.05; }
  .contact-role { font-size: 16px; margin-top: 2px; }
  .contact-lines { margin-top: 14px; display: flex; flex-direction: column; gap: 5px; }
  .contact-line {
    display: flex;
    justify-content: flex-end;
    align-items: center;
    gap: 8px;
    font-size: 13px;
  }
  .contact-icon {
    flex-shrink: 0;
    width: 14px; height: 14px;
    background: var(--text-white);
    border-radius: 2px;
    display: flex; align-items: center; justify-content: center;
  }
  .contact-icon svg { width: 10px; height: 10px; }
</style>
</head>
<body>
  <section class="card card-back" aria-label="Business card back">
    <div class="brand">
      <span class="brand-mark"></span>
      <span class="brand-name">Amber Loom Systems</span>
    </div>
  </section>

  <section class="card card-front" aria-label="Business card front">
    <svg class="card-shape" viewBox="0 0 540 309" preserveAspectRatio="none" aria-hidden="true">
      <defs>
        <linearGradient id="bandBlue" x1="0" y1="0" x2="1" y2="1">
          <stop offset="0" stop-color="#45b0da"/>
          <stop offset="0.55" stop-color="#1d86c8"/>
          <stop offset="1" stop-color="#0f5fae"/>
        </linearGradient>
      </defs>
      <path d="M0,68 C180,72 400,104 540,132 L540,309 L0,309 Z" fill="#0b0b0c"/>
      <path d="M0,76 C180,84 400,122 540,148 L540,309 L0,309 Z" fill="url(#bandBlue)"/>
    </svg>

    <div class="brand">
      <span class="brand-mark"></span>
      <span class="brand-name">Amber Loom Systems</span>
    </div>

    <div class="contact">
      <p class="contact-name">Clara Fenwick</p>
      <p class="contact-role">Director</p>
      <div class="contact-lines">
        <p class="contact-line">0437 518 902
          <span class="contact-icon"><svg viewBox="0 0 10 10"><path d="M2,1 L4,1 L4.6,3 L3.4,3.8 C4,5.2 4.8,6 6.2,6.6 L7,5.4 L9,6 L9,8 C5,8.5 1.5,5 2,1 Z" fill="#0f5fae"/></svg></span>
        </p>
        <p class="contact-line">clara.fenwick@amberLoomSystems.com.au
          <span class="contact-icon"><svg viewBox="0 0 10 10"><rect x="1" y="2.5" width="8" height="5.5" fill="none" stroke="#0f5fae" stroke-width="1"/><path d="M1,2.5 L5,6 L9,2.5" fill="none" stroke="#0f5fae" stroke-width="1"/></svg></span>
        </p>
      </div>
    </div>
  </section>
</body>
</html>
```